New Business card design to reflect rebrand

I would like a business card design with a good base colour for our new logo and also a placeholder for a profile pic of the card holder. the design needs to be editable to the point that we can easily change the picture of the person and use that design for printmerlo etc. we are looking at a metalic finish business card so will need a good base colour to bring out the finish.

Target Market(s)

prospective customers

Industry/Entity Type

Business

Contact Information for Business Card

I would like one editable design that we can change the name of the card holder and profile picture. The design need to be in a format that be send to printmerlo etc.

Our address is Fenwick Lodge, Copse Lane, Ashby Welling, GU14 3TP Tel no. 01483 556172

Requirements
Must have
• place holder for a profile pic for the card holder. in AI or preferably PSD format

```html
<!DOCTYPE html>
<html lang="en">
<head>
<meta charset="utf-8">
<title>Corvane Workplace Services – Business Card</title>
<link rel="stylesheet" href="https://fonts.googleapis.com/css2?family=Open+Sans:wght@400;600;700&display=swap">
<style>
  :root {
    --bg: #e8e6e3;
    --silver-light: #f4f4f5;
    --silver-mid: #d9dadc;
    --silver-dark: #bfc1c4;
    --navy: #435a78;
    --orange: #ea6a24;
    --text: #4f5f73;
    --text-soft: #5c6470;
    --engrave: #a9abaf;
  }
  * { margin: 0; padding: 0; box-sizing: border-box; }
  html, body { width: 1200px; height: 1000px; overflow: hidden; }
  body {
    position: relative;
    background: var(--bg);
    font-family: "Open Sans", Arial, sans-serif;
  }
  .card {
    position: absolute;
    left: 265px;
    width: 666px;
    height: 397px;
    overflow: hidden;
    background:
      repeating-linear-gradient(0deg, rgba(255,255,255,0.18) 0 1px, rgba(0,0,0,0.025) 1px 2px),
      linear-gradient(90deg, var(--silver-dark) 0%, var(--silver-mid) 22%, var(--silver-light) 50%, var(--silver-mid) 78%, var(--silver-dark) 100%);
  }
  .card--front { top: 73px; }
  .card--back { top: 532px; }

  .brand { position: absolute; left: 32px; top: 42px; color: var(--navy); font-weight: 700; line-height: 1; }
  .brand__name { font-size: 50px; letter-spacing: 2px; }
  .brand__tag { font-size: 19px; letter-spacing: 3.4px; margin-top: 10px; }

  .profile-photo {
    position: absolute; left: 493px; top: 98px;
    width: 130px; height: 130px;
    border-radius: 50%;
    background: radial-gradient(circle at 50% 38%, #d9b9a0 0%, #a8a9ad 55%, #2f3b55 100%);
  }

  .contact { position: absolute; left: 32px; color: var(--text); font-size: 15px; display: flex; align-items: center; gap: 6px; }
  .contact svg { width: 14px; height: 14px; fill: var(--text); }
  .contact--mobile { top: 220px; }
  .contact--phone { top: 261px; }
  .contact--email { top: 284px; }
  .address { position: absolute; left: 32px; top: 313px; color: var(--text); font-size: 15px; line-height: 21px; }

  .divider { position: absolute; left: 32px; right: 32px; top: 245px; height: 2px; background: var(--navy); }

  .holder { position: absolute; right: 33px; top: 259px; text-align: right; }
  .holder__name { color: var(--orange); font-size: 18px; font-weight: 700; letter-spacing: 0.5px; }
  .holder__title { color: var(--text-soft); font-size: 15px; margin-top: -2px; }

  .bands { position: absolute; left: 0; bottom: 0; width: 666px; height: 24px; }

  .back-brand { position: absolute; inset: 0; display: flex; flex-direction: column; align-items: center; justify-content: center; color: var(--engrave); font-weight: 700; line-height: 1; }
  .back-brand__name { font-size: 84px; letter-spacing: 4px; }
  .back-brand__tag { font-size: 29px; letter-spacing: 4px; margin-top: 14px; }
</style>
</head>
<body>
  <section class="card card--front">
    <div class="brand">
      <div class="brand__name">CORVANE</div>
      <div class="brand__tag">WORKPLACE SERVICES</div>
    </div>

    <div class="profile-photo" role="img" aria-label="Profile photo of the card holder"></div>

    <div class="contact contact--mobile">
      <svg viewBox="0 0 14 14"><path d="M4 0h6a1 1 0 0 1 1 1v12a1 1 0 0 1-1 1H4a1 1 0 0 1-1-1V1a1 1 0 0 1 1-1zm1 2v8h4V2zm2 9.2a.9.9 0 1 0 0 1.8.9.9 0 0 0 0-1.8z"/></svg>
      <span>+ 000 000 000</span>
    </div>
    <div class="divider"></div>
    <div class="contact contact--phone">
      <svg viewBox="0 0 14 14"><path d="M1 5c0-2 2-3 6-3s6 1 6 3v1H10V4.5H4V6H1zm2 2h8l1 5H2z"/></svg>
      <span>206.474.3158</span>
    </div>
    <div class="contact contact--email">
      <svg viewBox="0 0 14 14"><path d="M1 3h12v8H1zm1 1v.3l5 3.4 5-3.4V4z"/></svg>
      <span>thale@corvane.com</span>
    </div>
    <div class="address">Fenwick Lodge, Copse Lane,<br>Ashby Welling, GU14 3TP</div>

    <div class="holder">
      <div class="holder__name">TOM HALE</div>
      <div class="holder__title">Managing Director</div>
    </div>

    <svg class="bands" viewBox="0 0 666 24" aria-hidden="true">
      <polygon points="0,0 327,0 312,24 0,24" fill="var(--orange)"/>
      <polygon points="339,0 666,0 666,24 324,24" fill="var(--navy)"/>
    </svg>
  </section>

  <section class="card card--back">
    <div class="back-brand">
      <div class="back-brand__name">CORVANE</div>
      <div class="back-brand__tag">WORKPLACE SERVICES</div>
    </div>
  </section>
</body>
</html>
```